Dorwin's Coating & Renewal Letterhead Design We want to revamp out old traditional letterhead with the new logo designs that are attached. We are working on getting all our company items from vehicles, business, cards, t-shirts, letterhead to match. This should include company colors, fonts, and flow of items that we have attached below.

Industry/Entity Type

Construction Company

Font styles to use
Sans Serif
Other font styles liked:
• Bold with outline

Colors
ec1f27
ffffff

Requirements
Must have
• Company Name: Dorwin's Coating & Renewal
• Address: 4728 SW 81st Ter Halverd cove fl 39417
• Office Number: (555) 413-2986
• Email: Dorwinrenewal@mailbrook.example
• License Number: KRT8046392
Nice to have
• Company Colors: red, white, black, and grey

```html
<!DOCTYPE html>
<html lang="en">
<head>
<meta charset="utf-8">
<title>Dorwin's Coating &amp; Renewal — Letterhead</title>
<link href="https://fonts.googleapis.com/css2?family=Arimo:ital,wght@0,400;0,700;1,400&family=Tinos:wght@400;700&display=swap" rel="stylesheet">
<style>
  :root{
    --brand-red:#ec1f27;
    --deep-red:#a3151b;
    --ink:#1a1a1a;
    --grey:#9a9a9a;
    --body-grey:#6e6e6e;
    --paper:#ffffff;
    --backdrop:#d9dcde;
  }
  *{box-sizing:border-box;margin:0;padding:0}
  html,body{width:1200px;height:784px;overflow:hidden;background:var(--backdrop)}
  .letterhead{
    position:absolute;left:330px;top:22px;width:540px;height:740px;
    background:var(--paper);box-shadow:0 6px 18px rgba(0,0,0,.18);
    overflow:hidden;font-family:"Arimo",Arial,sans-serif;
  }
  .corner{position:absolute}
  .corner--right{right:0;top:190px;width:90px;height:190px}
  .corner--left{left:0;top:400px;width:90px;height:230px}
  .brand{
    position:absolute;top:46px;right:52px;text-align:right;
    display:flex;align-items:center;gap:10px;
  }
  .brand__mark{width:14px;height:14px;background:var(--brand-red);border-radius:50%}
  .brand__name{
    font-family:"Arimo",Arial,sans-serif;font-weight:700;font-size:20px;
    color:var(--brand-red);line-height:1.1;letter-spacing:.2px;
  }
  .letter-body{
    position:absolute;top:120px;left:92px;right:92px;
    font-size:9.6px;line-height:1.5;color:var(--body-grey);text-align:justify;
  }
  .letter-body p{margin-bottom:11px}
  .contact{
    position:absolute;left:0;right:0;bottom:42px;text-align:center;
    font-family:"Tinos","Times New Roman",serif;color:#555;
  }
  .contact__icons{display:flex;justify-content:center;gap:8px;margin-bottom:7px}
  .contact__icons svg{width:15px;height:15px}
  .contact__address{color:var(--brand-red);font-weight:700;font-size:11px;margin-bottom:3px}
  .contact__line{font-size:9.5px;line-height:1.45}
  .contact__sep{color:var(--brand-red);padding:0 5px}
  .rule{position:absolute;bottom:86px;height:1px;width:130px;background:#888}
  .rule--left{left:60px}
  .rule--right{right:60px}
</style>
</head>
<body>
<main class="letterhead">

  <svg class="corner corner--right" viewBox="0 0 90 190" aria-hidden="true">
    <defs>
      <linearGradient id="redFadeR" x1="0" y1="0" x2="1" y2="1">
        <stop offset="0" stop-color="var(--brand-red)"/><stop offset="1" stop-color="#8e1218"/>
      </linearGradient>
    </defs>
    <polygon points="90,0 90,160 62,148" fill="url(#redFadeR)"/>
    <polygon points="90,0 62,148 54,158 74,0" fill="#111"/>
    <polygon points="74,0 54,158 50,164 68,0" fill="#fff"/>
    <polygon points="68,0 50,164 44,172 62,0" fill="var(--grey)"/>
    <polygon points="44,172 90,190 90,180 54,158" fill="#c7c7c7"/>
  </svg>

  <svg class="corner corner--left" viewBox="0 0 90 230" aria-hidden="true">
    <defs>
      <linearGradient id="redFadeL" x1="1" y1="0" x2="0" y2="1">
        <stop offset="0" stop-color="#8e1218"/><stop offset="1" stop-color="var(--brand-red)"/>
      </linearGradient>
    </defs>
    <polygon points="0,10 30,20 0,230" fill="url(#redFadeL)"/>
    <polygon points="0,0 44,14 18,230 10,230 34,20 0,8" fill="#111"/>
    <polygon points="44,14 52,10 26,230 18,230" fill="#fff"/>
    <polygon points="52,10 60,6 34,230 26,230" fill="var(--grey)"/>
  </svg>

  <header class="brand">
    <span class="brand__mark" aria-hidden="true"></span>
    <span class="brand__name">Dorwin's<br>Coating &amp; Renewal</span>
  </header>

  <section class="letter-body">
    <p>Lorem Ipsum is simply dummy text of the printing and typesetting industry. Lorem Ipsum has been the industry's standard dummy text ever since the 1500s, when an unknown printer took a galley of type and scrambled it to make a type specimen book. It has survived not only five centuries, but also the leap into electronic typesetting, remaining essentially unchanged. It was popularised in the 1960s with the release of Tranfield sheets containing Lorem Ipsum passages, and more recently with desktop publishing software like Quillset Layout including versions of Lorem Ipsum.</p>
    <p>It is a long established fact that a reader will be distracted by the readable content of a page when looking at its layout. The point of using Lorem Ipsum is that it has a more-or-less normal distribution of letters, as opposed to using 'Content here, content here', making it look like readable English. Many desktop publishing packages and web page editors now use Lorem Ipsum as their default model text, and a search for 'lorem ipsum' will uncover many web sites still in their infancy. Various versions have evolved over the years, sometimes by accident, sometimes on purpose (injected humour and the like).</p>
    <p>Contrary to popular belief, Lorem Ipsum is not simply random text. It has roots in a piece of classical Latin literature from 45 BC, making it over 2000 years old. Harold Venmore, a Latin professor at Brackwater College in Virginia, looked up one of the more obscure Latin words, consectetur, from a Lorem Ipsum passage, and going through the cites of the word in classical literature, discovered the undoubtable source. Lorem Ipsum comes from sections 1.10.32 and 1.10.33 of "de Finibus Bonorum et Malorum" structures, to generate Lorem Ipsum which looks reasonable. The generated Lorem Ipsum is therefore always free from repetition, injected humour, or non-characteristic words etc.</p>
  </section>

  <span class="rule rule--left" aria-hidden="true"></span>
  <span class="rule rule--right" aria-hidden="true"></span>

  <footer class="contact">
    <div class="contact__icons" aria-hidden="true">
      <svg viewBox="0 0 16 16"><circle cx="8" cy="8" r="8" fill="var(--brand-red)"/><path d="M8 3.5a3 3 0 0 0-3 3c0 2.2 3 6 3 6s3-3.8 3-6a3 3 0 0 0-3-3z" fill="#fff"/><circle cx="8" cy="6.5" r="1.1" fill="var(--brand-red)"/></svg>
      <svg viewBox="0 0 16 16"><circle cx="8" cy="8" r="8" fill="var(--brand-red)"/><path d="M5.5 4h1.6l.7 2-1 .8a6 6 0 0 0 2.4 2.4l.8-1 2 .7v1.6c0 .5-.5.9-1 .8A7 7 0 0 1 4.7 5c-.1-.5.3-1 .8-1z" fill="#fff"/></svg>
      <svg viewBox="0 0 16 16"><circle cx="8" cy="8" r="8" fill="var(--brand-red)"/><circle cx="8" cy="8" r="3.5" fill="none" stroke="#fff" stroke-width="1.3"/></svg>
      <svg viewBox="0 0 16 16"><circle cx="8" cy="8" r="8" fill="var(--brand-red)"/><rect x="4" y="5" width="8" height="6" rx=".6" fill="#fff"/><path d="M4.3 5.4 8 8.3l3.7-2.9" fill="none" stroke="var(--brand-red)" stroke-width=".9"/></svg>
      <svg viewBox="0 0 16 16"><circle cx="8" cy="8" r="8" fill="var(--brand-red)"/><g fill="none" stroke="#fff" stroke-width=".9"><circle cx="8" cy="8" r="4"/><ellipse cx="8" cy="8" rx="1.8" ry="4"/><path d="M4 8h8"/></g></svg>
    </div>
    <p class="contact__address">4728 SW 81st Ter Halverd cove fl 39417</p>
    <p class="contact__line">(555) 413-2986<span class="contact__sep">|</span>License: KRT8046392</p>
    <p class="contact__line">Dorwinrenewal@mailbrook.example<span class="contact__sep">|</span>www.dorwinrenewal.example</p>
  </footer>

</main>
</body>
</html>
```